Tall Fern Roofing Business Card

Need a business card with the logo that was designed here

Contact Information for Business Card

Name, Title, Phone, Email, Website, Company name

```html
<!DOCTYPE html>
<html lang="en">
<head>
<meta charset="utf-8">
<title>Tall Fern Roofing – Business Card</title>
<link href="https://fonts.googleapis.com/css2?family=Open+Sans:wght@400;700&display=swap" rel="stylesheet">
<style>
  :root{
    --bg:#4a4a4a;
    --card:#ffffff;
    --blue:#1f74bd;
    --grey:#96979b;
    --ink:#2b2b2b;
  }
  *{box-sizing:border-box;margin:0;padding:0}
  html,body{width:1200px;height:801px;overflow:hidden}
  body{background:var(--bg);font-family:"Open Sans",Arial,sans-serif;position:relative}
  .card{
    position:absolute;top:246px;width:540px;height:309px;
    background:var(--card);border-radius:18px;overflow:hidden;
    box-shadow:0 10px 24px rgba(0,0,0,.35);
  }
  .card--front{left:45px}
  .card--back{left:615px}

  .swoosh{position:absolute;left:0;bottom:0;width:540px;height:309px}

  .brand{
    display:flex;align-items:center;gap:8px;
    color:var(--blue);font-weight:700;white-space:nowrap;
  }
  .brand__mark{background:var(--grey);flex:none}
  .card--front .brand{position:absolute;left:28px;top:120px;font-size:19px}
  .card--front .brand__mark{width:14px;height:14px}

  .divider{position:absolute;left:240px;top:58px;width:1.5px;height:150px;background:var(--blue)}

  .contact{position:absolute;left:262px;top:52px;color:var(--ink);font-size:12.5px;line-height:1.38}
  .contact__name{color:var(--blue);font-weight:700;font-size:19px;line-height:1.1;letter-spacing:.2px}
  .contact__title{margin-bottom:14px}
  .contact__address{margin-bottom:14px}
  .contact__row{display:flex;align-items:center;gap:6px}
  .contact__row svg{width:11px;height:11px;flex:none}

  .card--back .brand{position:absolute;left:0;right:0;top:0;bottom:0;justify-content:center;font-size:38px;gap:14px}
  .card--back .brand__mark{width:28px;height:28px}
</style>
</head>
<body>

<section class="card card--front" aria-label="Business card front">
  <svg class="swoosh" viewBox="0 0 540 309" aria-hidden="true">
    <path d="M0 309 L0 300 C160 300 420 250 540 150 L540 158 C420 265 170 306 20 309 Z" fill="var(--grey)"/>
    <path d="M30 309 C200 300 430 260 540 175 L540 309 Z" fill="var(--blue)"/>
  </svg>

  <div class="brand">
    <span class="brand__mark"></span>
    <span class="brand__name">Tall Fern Roofing</span>
  </div>

  <div class="divider"></div>

  <div class="contact">
    <div class="contact__name">OWEN HARTLEY</div>
    <div class="contact__title">Managing Director</div>
    <div class="contact__address">Your address, City<br>State, Zip 1234</div>
    <div class="contact__row">
      <svg viewBox="0 0 12 12"><circle cx="6" cy="6" r="6" fill="var(--blue)"/><path d="M4 3.2 5 3 5.6 4.6 4.9 5.2C5.3 6 6 6.7 6.8 7.1L7.4 6.4 9 7 8.8 8C6 8.2 3.8 6 4 3.2Z" fill="#fff"/></svg>
      <span>123 456 789</span>
    </div>
    <div class="contact__row">
      <svg viewBox="0 0 12 12"><rect x="0.5" y="2.5" width="11" height="7" rx="1" fill="var(--blue)"/><path d="M1 3 6 7 11 3" stroke="#fff" stroke-width="1" fill="none"/></svg>
      <span>info@yourgmail.com</span>
    </div>
    <div class="contact__row">
      <svg viewBox="0 0 12 12"><circle cx="6" cy="6" r="5.5" fill="var(--blue)"/><path d="M.5 6H11.5M6 .5C3.5 3.5 3.5 8.5 6 11.5M6 .5C8.5 3.5 8.5 8.5 6 11.5" stroke="#fff" stroke-width=".8" fill="none"/></svg>
      <span>www.yourwebsite.com</span>
    </div>
  </div>
</section>

<section class="card card--back" aria-label="Business card back">
  <div class="brand">
    <span class="brand__mark"></span>
    <span class="brand__name">Tall Fern Roofing</span>
  </div>
</section>

</body>
</html>
```